TA BRAMLEY BUSINESS CARD DESIGN PROJECT

We need to utilize our logo that was expertly created on PixelHarbor and now need to match this with a business card design.

```html
<!DOCTYPE html>
<html lang="en">
<head>
<meta charset="utf-8">
<title>TA Bramley Business Card</title>
<link href="https://fonts.googleapis.com/css2?family=Montserrat:wght@400;500;700;800&display=swap" rel="stylesheet">
<style>
  :root {
    --page: #d9d9db;
    --card: #1b1b1d;
    --card-edge: #2a2a2d;
    --brand-blue: #1a5ec4;
    --emboss: #2e2e31;
    --text-light: #f2f2f2;
  }
  * { margin: 0; padding: 0; box-sizing: border-box; }
  html, body {
    width: 1200px; height: 900px; overflow: hidden;
    background: var(--page);
    font-family: "Montserrat", sans-serif;
  }
  .sheet {
    width: 1200px; height: 900px;
    display: flex; flex-direction: column; align-items: center; justify-content: center;
    gap: 48px;
  }
  .card {
    width: 700px; height: 400px;
    background: var(--card);
    border-radius: 28px;
    box-shadow: 0 14px 30px rgba(0,0,0,.28);
    position: relative;
    overflow: hidden;
  }
  .card-front { display: flex; align-items: center; justify-content: center; }
  .front-wordmark {
    font-weight: 800;
    font-size: 78px;
    letter-spacing: 10px;
    color: var(--emboss);
  }
  .card-back { display: flex; align-items: center; }
  .back-brand {
    width: 370px;
    display: flex; align-items: center; justify-content: center;
  }
  .back-wordmark {
    font-weight: 800;
    font-size: 38px;
    letter-spacing: 5px;
    color: var(--brand-blue);
  }
  .divider {
    width: 2px; height: 250px;
    background: var(--brand-blue);
  }
  .contact {
    padding-left: 36px;
    color: var(--text-light);
  }
  .contact-name {
    font-weight: 700; font-size: 22px; letter-spacing: .5px;
    color: var(--brand-blue);
  }
  .contact-role { font-size: 15px; margin-top: 2px; margin-bottom: 20px; }
  .contact-list { list-style: none; }
  .contact-list li {
    display: flex; align-items: center; gap: 10px;
    font-size: 15px; line-height: 1.75;
  }
  .contact-list svg { width: 14px; height: 14px; fill: var(--brand-blue); flex: none; }
  .contact-address { font-size: 15px; line-height: 1.4; margin-top: 16px; padding-left: 24px; }
</style>
</head>
<body>
<main class="sheet">
  <section class="card card-front">
    <span class="front-wordmark">TA BRAMLEY</span>
  </section>

  <section class="card card-back">
    <div class="back-brand">
      <span class="back-wordmark">TA BRAMLEY</span>
    </div>
    <div class="divider"></div>
    <div class="contact">
      <p class="contact-name">DANIEL REEVE</p>
      <p class="contact-role">Managing Director</p>
      <ul class="contact-list">
        <li>
          <svg viewBox="0 0 16 16"><path d="M3 1h3l1.5 4-2 1.2a9 9 0 0 0 4.3 4.3L11 8.5l4 1.5v3a2 2 0 0 1-2 2A12 12 0 0 1 1 3a2 2 0 0 1 2-2z"/></svg>
          555 014 2290
        </li>
        <li>
          <svg viewBox="0 0 16 16"><path d="M4 1h7v4H4zM2 6h12a1 1 0 0 1 1 1v6a1 1 0 0 1-1 1H2a1 1 0 0 1-1-1V7a1 1 0 0 1 1-1zm2 2v2h2V8zm3 0v2h2V8zm3 0v2h2V8z"/></svg>
          555 014 2291
        </li>
        <li>
          <svg viewBox="0 0 16 16"><path d="M1 3h14v1.2L8 9 1 4.2zM1 6l7 4.8L15 6v7H1z"/></svg>
          info@tabramley.com
        </li>
        <li>
          <svg viewBox="0 0 16 16"><circle cx="8" cy="8" r="7"/></svg>
          www.tabramley.com
        </li>
      </ul>
      <p class="contact-address">Your address, City<br>State, Zip 1234</p>
    </div>
  </section>
</main>
</body>
</html>
```